Can you make our site AWESOME?

Hi Guys,

I am a co-founder of Tallow Crate Rentals Australia, the world's first e-commerce skip bin business.

We are looking to update our site before a launch into the UK in March.

Please help us by submitting your designs for the following pages:

- Home page (www.tallowcraterentals.example.au)
- About us (https://www.tallowcraterentals.example.au/pages/about-us
- Contact us (https://www.tallowcraterentals.example.au/pages/contact-us)
- Quick Quote / Pricing (https://www.tallowcraterentals.example.au/pages/free-instant-quote-skip-bin-hire)

NOTES:
- Design should be high-converting
- best designs will be fresh, modern, easy to read, distinctive and memorable
- please use our logo and video colours
- feel free to change logos, layout, images and anything else you feel can be improved
- the winning designer will potentially have the opportunity to re-design the other pages on our site
- brief is for design only

Any questions just ask.

Thanks,
Oliver

```html
<!DOCTYPE html>
<html lang="en">
<head>
<meta charset="utf-8">
<title>Tallow Crate Rentals Australia</title>
<link href="https://fonts.googleapis.com/css2?family=Lato:wght@400;700;900&display=swap" rel="stylesheet">
<style>
:root{
  --navy:#1f2150;
  --navy-deep:#1b1d48;
  --green:#2a7a3b;
  --green-bright:#2f8a3f;
  --grey-bg:#efefef;
  --text:#333;
  --muted:#555;
  --white:#fff;
}
*{box-sizing:border-box;margin:0;padding:0}
html,body{width:1200px;height:4157px;overflow:hidden}
body{font-family:'Lato',sans-serif;color:var(--text);background:var(--white);position:relative}
.abs{position:absolute}
a{color:inherit;text-decoration:none}
.pill{display:flex;align-items:center;justify-content:center;border-radius:30px;font-weight:700;font-size:14px;letter-spacing:.5px}
.pill-green{background:var(--green);color:var(--white)}
.pill-white{background:var(--white);color:var(--navy)}

/* header */
.site-header{top:0;left:0;width:1200px;height:83px;background:var(--white)}
.brand{left:75px;top:22px;display:flex;align-items:center;gap:12px}
.brand-mark{width:34px;height:34px;background:var(--green);border-radius:4px}
.brand-name{font-weight:900;font-size:18px;color:var(--navy);letter-spacing:.5px;line-height:1.1;width:200px}
.call-now{left:752px;top:33px;font-weight:700;font-size:15px;color:var(--navy)}
.btn-account{left:962px;top:24px;width:163px;height:36px}
.main-nav{top:83px;left:0;width:1200px;height:54px;background:var(--navy)}
.main-nav span{position:absolute;top:19px;color:var(--white);font-size:13px;font-weight:700;letter-spacing:.5px}

/* hero */
.hero{top:137px;left:0;width:1200px;height:700px;background:linear-gradient(100deg,#c9b226 0%,#d8c33a 22%,#2b7a3c 38%,#3f9a4d 52%,#2b4fa0 68%,#1f3b8a 85%,#3a3a44 100%)}
.hero-shade{top:137px;left:0;width:1200px;height:700px;background:rgba(20,20,40,.25)}
.hero-title{top:370px;left:0;width:1200px;text-align:center;color:var(--white);font-weight:900;font-size:41px}
.hero-sub{top:426px;left:0;width:1200px;text-align:center;color:var(--white);font-weight:700;font-size:24px}
.search{height:48px;background:var(--white);border-radius:26px;display:flex;align-items:center;justify-content:space-between;padding:0 20px;font-size:13px;color:#444;box-shadow:0 1px 3px rgba(0,0,0,.15)}
.hero-search{left:275px;top:470px;width:460px}
.hero-call{left:748px;top:470px;width:174px;height:48px}
.wave{left:0;width:1200px}

/* audience cards */
.aud-card{top:920px;width:330px;height:308px;background:linear-gradient(180deg,#1f3358 0%,#24504a 55%,#2a6c40 100%);color:var(--white);text-align:center}
.aud-card svg{margin-top:42px}
.aud-card h3{font-size:24px;font-weight:700;margin-top:12px}
.aud-card p{font-size:13px;line-height:21px;margin:10px auto 0;width:270px}
.aud-card .pill{width:176px;height:42px;margin:22px auto 0}
.arrow{font-size:40px;color:#777;font-weight:300}

/* rating */
.rating-bg{top:1310px;left:0;width:1200px;height:480px}
.video{left:75px;top:1372px;width:512px;height:340px;background:linear-gradient(180deg,#5a5a86 0%,#4a4a78 60%,#3a6a4a 85%,#2e2e40 100%)}
.play{left:307px;top:1518px;width:48px;height:48px;border-radius:50%;background:rgba(255,255,255,.85)}
.rating-title{left:647px;top:1435px;width:480px;font-size:32px;line-height:42px;color:var(--navy);font-weight:400}
.btn-video{left:647px;top:1600px;width:176px;height:43px}

/* steps */
.section-title{left:0;width:1200px;text-align:center;color:var(--navy);font-size:34px;font-weight:400}
.step{top:1905px;width:340px;text-align:center}
.step-art{width:110px;height:100px;margin:0 auto;border-radius:50%;background:radial-gradient(circle,#5a6090 0%,#2c3266 70%)}
.step h3{color:var(--green);font-size:24px;font-weight:700;margin-top:30px}
.step p{font-size:13px;line-height:22px;color:var(--muted);width:250px;margin:10px auto 0}
.steps-note{top:2203px;left:0;width:1200px;text-align:center;font-size:13px;font-weight:700;color:var(--navy)}

/* benefits */
.benefit-band{top:2270px;left:0;width:1200px;height:610px}
.benefit{top:2445px;width:240px;height:337px;background:var(--white);text-align:center}
.benefit-art{width:80px;height:66px;margin:28px auto 0;border-radius:50%;background:radial-gradient(circle,#3c8d4c 0%,#1f2150 80%)}
.benefit h3{color:var(--green);font-size:22px;line-height:27px;font-weight:700;margin-top:12px}
.benefit p{font-size:13px;line-height:21px;color:var(--muted);width:200px;margin:8px auto 0}

/* testimonial */
.quote-head{top:3000px;left:0;width:1200px;text-align:center;color:var(--green);font-weight:700;font-size:18px}
.quote{top:3033px;left:240px;width:720px;text-align:center;font-size:17px;line-height:29px;color:#333}
.stars{top:3143px;left:0;width:1200px;display:flex;justify-content:center;gap:3px}
.quote-name{top:3170px;left:0;width:1200px;text-align:center;color:var(--green);font-weight:700;font-size:16px}
.quote-date{top:3193px;left:0;width:1200px;text-align:center;color:#444;font-size:16px}

/* cta */
.cta-text{top:3418px;left:0;width:1200px;text-align:center;font-size:16px;color:#333}
.cta-search{left:275px;top:3460px;width:460px;border:1px solid #ddd}
.cta-call{left:748px;top:3460px;width:174px;height:48px}

/* footer */
.footer-bg{top:3570px;left:0;width:1200px;height:530px}
.foot-col{top:3813px;color:var(--white)}
.foot-col h4{font-size:16px;font-weight:700;margin-bottom:16px}
.foot-col li{list-style:none;font-size:13px;line-height:32px}
.foot-col p{font-size:13px;line-height:21px;width:320px}
.news-input{width:310px;height:34px;background:var(--white);border-radius:18px;margin-top:18px;padding:0 14px;display:flex;align-items:center;color:#444;font-size:13px}
.btn-signup{width:120px;height:36px;margin:12px 0 0 190px}
.bottom-bar{top:4097px;left:0;width:1200px;height:60px;background:var(--green)}
.copyright{left:75px;top:22px;color:var(--white);font-size:12px}
.social{right:75px;top:20px;display:flex;gap:14px}
.social span{width:18px;height:18px;border-radius:50%;background:var(--white);display:block}
</style>
</head>
<body>

<header class="site-header abs">
  <div class="brand abs"><span class="brand-mark"></span><span class="brand-name">Tallow Crate Rentals Australia</span></div>
  <div class="call-now abs">CALL NOW: 1800 555 019</div>
  <a class="btn-account abs pill pill-green">CREATE ACCOUNT</a>
</header>
<nav class="main-nav abs">
  <span style="left:75px">PRICING</span>
  <span style="left:190px">LEARN MORE</span>
  <span style="left:338px">ABOUT</span>
  <span style="left:443px">TRADE SECRETS</span>
  <span style="left:610px">CONTACT</span>
  <span style="left:1070px">&#128722; CART</span>
</nav>

<section>
  <div class="hero abs" role="img" aria-label="Photo of yellow, green and blue wheelie bins"></div>
  <div class="hero-shade abs"></div>
  <h1 class="hero-title abs">1000's of Skips at Your Finger Tips</h1>
  <p class="hero-sub abs">Best Service &amp; Price | Hassle Free | Australia Wide</p>
  <div class="search hero-search abs"><span>Enter Postcode or Suburb</span>
    <svg width="16" height="16" viewBox="0 0 16 16"><circle cx="6.5" cy="6.5" r="5" fill="none" stroke="#222" stroke-width="2"/><line x1="10" y1="10" x2="15" y2="15" stroke="#222" stroke-width="2.4"/></svg></div>
  <a class="hero-call abs pill pill-green">CALL US</a>
  <svg class="wave abs" style="top:660px" width="1200" height="180" viewBox="0 0 1200 180" preserveAspectRatio="none">
    <path d="M0 120 C250 160 420 190 640 110 C820 40 1000 20 1200 60 L1200 180 L0 180Z" fill="#2a7a3b"/>
    <path d="M0 140 C250 180 430 200 650 125 C830 60 1000 40 1200 80 L1200 180 L0 180Z" fill="#fff"/>
  </svg>
</section>

<section>
  <span class="arrow abs" style="left:40px;top:1045px">&#8249;</span>
  <span class="arrow abs" style="left:1140px;top:1045px">&#8250;</span>
  <div class="aud-card abs" style="left:75px">
    <svg width="56" height="48" viewBox="0 0 56 48"><path d="M28 2 L2 24 L9 24 L9 46 L22 46 L22 32 L34 32 L34 46 L47 46 L47 24 L54 24Z" fill="#fff"/></svg>
    <h3>Renovators</h3><p>Make sure skip bin hire is one less thing to worry about.</p>
    <a class="pill pill-white">LEARN MORE</a></div>
  <div class="aud-card abs" style="left:435px">
    <svg width="56" height="48" viewBox="0 0 56 48"><path d="M44 4a11 11 0 0 0-13 14L8 41l5 5 23-23a11 11 0 0 0 14-13l-7 7-6-2-2-6z" fill="#fff"/></svg>
    <h3>Tradie</h3><p>From Australia's fastest growing Skip Bin Hire company</p>
    <a class="pill pill-white">LEARN MORE</a></div>
  <div class="aud-card abs" style="left:795px">
    <svg width="56" height="48" viewBox="0 0 56 48"><rect x="16" y="2" width="24" height="44" fill="#fff"/><g fill="#245a48"><rect x="20" y="7" width="5" height="5"/><rect x="31" y="7" width="5" height="5"/><rect x="20" y="16" width="5" height="5"/><rect x="31" y="16" width="5" height="5"/><rect x="20" y="25" width="5" height="5"/><rect x="31" y="25" width="5" height="5"/><rect x="25" y="36" width="6" height="10"/></g></svg>
    <h3>Builders</h3><p>Form Australia's highest star rated Skip Bin Hire company.</p>
    <a class="pill pill-white">LEARN MORE</a></div>
</section>

<section>
  <svg class="rating-bg abs" width="1200" height="480" viewBox="0 0 1200 480" preserveAspectRatio="none"><path d="M0 0 H1200 V430 C900 470 400 480 0 455Z" fill="#efefef"/></svg>
  <div class="video abs" role="img" aria-label="Video still of an animated house with a skip bin"></div>
  <div class="play abs"></div>
  <svg class="abs" style="left:324px;top:1531px" width="18" height="22" viewBox="0 0 18 22"><path d="M0 0 L18 11 L0 22Z" fill="#4a4a78"/></svg>
  <h2 class="rating-title abs">Australia's Highest Rated Skip Bin Hire Company - Rated by You</h2>
  <a class="btn-video abs pill pill-green">WATCH VIDEO</a>
</section>

<section>
  <h2 class="section-title abs" style="top:1825px">As Easy As 1, 2, 3...</h2>
  <div class="step abs" style="left:70px"><div class="step-art" role="img" aria-label="Illustration of chat bubbles"></div><h3>Simple, Easy Booking</h3><p>Call 1800 555 019 or click here to get started with your instant quote</p></div>
  <div class="step abs" style="left:430px"><div class="step-art" role="img" aria-label="Illustration of a laptop with confirmation"></div><h3>Instant Confirmation</h3><p>Receive your booking details and a 30 minute courtesy call before drop off</p></div>
  <div class="step abs" style="left:790px"><div class="step-art" role="img" aria-label="Illustration of a skip bin with 24 hour badge"></div><h3>Gone When Your Ready!</h3><p>Let us know and your bin will be gone within 24hrs</p></div>
  <p class="steps-note abs">We manage your booking from start to finish, so you can focus on other things</p>
</section>

<section>
  <svg class="benefit-band abs" width="1200" height="610" viewBox="0 0 1200 610" preserveAspectRatio="none">
    <defs><linearGradient id="band" x1="0" y1="0" x2="1" y2="0"><stop offset="0" stop-color="#2a7a3b"/><stop offset=".55" stop-color="#1f4a4a"/><stop offset="1" stop-color="#1f2150"/></linearGradient></defs>
    <path d="M0 0 C300 40 700 60 1200 20 V530 C800 560 400 590 0 610Z" fill="url(#band)"/></svg>
  <h2 class="section-title abs" style="top:2365px;color:#fff">Save Time. Save Money.</h2>
  <div class="benefit abs" style="left:75px"><div class="benefit-art" role="img" aria-label="Map of Australia with location pin"></div><h3>Any Bin, Anytime, Anywhere</h3><p>We connect you with local companies Australia wide; for faster response times, less km's and emissions, greater reliability and lower prices</p></div>
  <div class="benefit abs" style="left:347px"><div class="benefit-art" role="img" aria-label="Customer service agent with headset"></div><h3>Service Guaranteed</h3><p>Want to speak to someone when it suits you? We answer the phones and return calls from 7.30am to 8pm 7 days a week</p></div>
  <div class="benefit abs" style="left:617px"><div class="benefit-art" role="img" aria-label="Cash and coins"></div><h3>Best<br>Pricing</h3><p>We've done the hard work behind the scenes, so with one click you have your best priced, local skip</p></div>
  <div class="benefit abs" style="left:887px"><div class="benefit-art" role="img" aria-label="Handshake"></div><h3>First Class Supply Partners</h3><p>Our local supply partners are the best in the business and share our passion for making you happy</p></div>
</section>

<section>
  <h2 class="section-title abs" style="top:2955px">Five Star Service</h2>
  <p class="quote-head abs">Great Service</p>
  <p class="quote abs">Prompt, reliable and cooperative service. We had particular needs in relation to where the skip had to be placed for access, and also drop-off and collection times. Everything was perfect. Thank you</p>
  <span class="arrow abs" style="left:118px;top:3075px">&#8249;</span>
  <span class="arrow abs" style="left:1062px;top:3075px">&#8250;</span>
  <div class="stars abs">
    <svg width="100" height="18" viewBox="0 0 100 18"><g fill="#2a7a3b"><path id="st" d="M9 0l2.6 5.8 6.4.6-4.8 4.2 1.4 6.3L9 13.6 3.4 16.9l1.4-6.3L0 6.4l6.4-.6z"/><use href="#st" x="20"/><use href="#st" x="40"/><use href="#st" x="60"/><use href="#st" x="80"/></g></svg>
  </div>
  <p class="quote-name abs">Marcus Pendleton</p>
  <p class="quote-date abs">20/05/2018</p>
</section>

<section>
  <h2 class="section-title abs" style="top:3355px">We're ready to go!</h2>
  <p class="cta-text abs">To book, ask questions or just for a chat, call us 7 days a week, 7.30am to 8pm</p>
  <div class="search cta-search abs"><span>Enter Postcode or Suburb</span>
    <svg width="16" height="16" viewBox="0 0 16 16"><circle cx="6.5" cy="6.5" r="5" fill="none" stroke="#222" stroke-width="2"/><line x1="10" y1="10" x2="15" y2="15" stroke="#222" stroke-width="2.4"/></svg></div>
  <a class="cta-call abs pill pill-green">CALL US</a>
</section>

<footer>
  <svg class="footer-bg abs" width="1200" height="530" viewBox="0 0 1200 530" preserveAspectRatio="none">
    <path d="M0 0 H1200 V180 H0Z" fill="#efefef"/>
    <path d="M0 110 C200 150 350 160 560 90 C780 20 1000 30 1200 100 V530 H0Z" fill="#1f2150"/></svg>
  <div class="foot-col abs" style="left:75px"><h4>Tallow Crate Rentals - Australia Wide</h4>
    <ul><li>Sydney</li><li>Melbourne</li><li>Brisbane</li><li>Perth</li><li>Adelaide</li><li>Canberra</li></ul></div>
  <div class="foot-col abs" style="left:420px"><h4>Learn More</h4>
    <ul><li>Waste Types</li><li>Skip Bin Sizes</li><li>Refund Policy</li><li>Pay Later with Spreadly</li><li>FAQ</li><li>Privacy</li></ul></div>
  <div class="foot-col abs" style="left:705px"><h4>Latest Industry News</h4>
    <p>Sign up for the latest news, offers from TALLOW CRATE RENTALS AUSTRALIA</p>
    <div class="news-input">Enter Email Address</div>
    <a class="btn-signup pill pill-green">SIGN UP</a></div>
  <div class="bottom-bar abs">
    <p class="copyright abs">Copyright © 2019 Company Name. All Right Reserved</p>
    <div class="social abs" aria-label="Social links"><span></span><span></span><span></span><span></span><span></span></div>
  </div>
</footer>

</body>
</html>
```